Sheep pen surround needed

Large size- 20ft wide by 2.7ft high
Please see image for basic guide as to what I am looking for. Looking to be inspired so open to new ideas also.
Background should be off-white to cream- happy to see other colours though.
Wild flowers from the bottom- please ensure they look naturally placed-different heights etc. Also happy for you to source other wild flower images- would be great to see thistles.
Bunting with logo on top (I would like the bunting to look real- please add a shadow behind it ect)
Please match greens to banner shown.
Open to ideas.
Please can you edit the colours to match logo and banner (Banner will be above the pen)
PLEASE ENSURE THAT THE ENDS MATCH UP- If the banner is linked together.
Hello
Thank you for your help so far, however, I feel that the designs I have been sent have been very basic and not much better than I can produce myself.
I'm looking for - Wild flowers to look natural - differing heights etc - not just quickly placed.
The bunting flags- should look like bunting - I want this to be realistic with shadowing behind it to make it look 3D.
Either end of the design must match up - e.g if I were to link up the design it would fit together.
I would like to see different options using my new logo placed in different positions.
I'm open to ideas- looking to be inspired please :)

```html
<!DOCTYPE html>
<html lang="en">
<head>
<meta charset="utf-8">
<title>Fernlea Sheep Pen Surround</title>
<link href="https://fonts.googleapis.com/css2?family=Cinzel:wght@600&display=swap" rel="stylesheet">
<style>
  :root {
    --page: #ffffff;
    --cream: #efeee9;
    --band: #d7d7d7;
    --string: #545c36;
    --olive-dark: #5f6838;
    --olive-light: #a9b07a;
    --flag-white: #ffffff;
    --ink: #3b3f2a;
    --meadow-top: rgba(239, 238, 233, 0);
    --meadow-mid: #c9b2dc;
    --meadow-low: #7fb347;
    --meadow-base: #4f8f2a;
  }
  * { margin: 0; padding: 0; box-sizing: border-box; }
  html, body { width: 1200px; height: 1200px; overflow: hidden; background: var(--page); }
  .sheet { position: relative; width: 1200px; height: 1200px; }
  .pen-panel {
    position: absolute;
    background: var(--cream);
    overflow: hidden;
  }
  .pen-panel--full { left: 24px; top: 386px; width: 1160px; height: 167px; }
  .pen-panel--left { left: 25px; top: 664px; width: 576px; height: 167px; }
  .pen-panel--right { left: 605px; top: 664px; width: 581px; height: 167px; }
  .meadow {
    position: absolute; left: 0; right: 0; bottom: 0; height: 108px;
    background: linear-gradient(to bottom, var(--meadow-top) 0%, var(--meadow-mid) 35%, var(--meadow-low) 75%, var(--meadow-base) 100%);
  }
  .bunting { position: absolute; inset: 0; width: 100%; height: 100%; }
  .flag { filter: drop-shadow(3px 5px 3px rgba(0,0,0,0.28)); }
  .flag-name, .crest-name {
    font-family: "Cinzel", serif; font-weight: 600; fill: var(--ink); text-anchor: middle;
  }
  .flag-name { font-size: 7px; }
  .crest-name { font-size: 15px; }
</style>
</head>
<body>
<main class="sheet">

  <!-- Full-length panel -->
  <section class="pen-panel pen-panel--full">
    <div class="meadow" role="img" aria-label="Meadow of wild flowers at varied heights: thistles, poppies, cornflowers, tansy, willowherb and daisies in grass"></div>
    <svg class="bunting" viewBox="0 0 1160 167" aria-hidden="false">
      <defs>
        <linearGradient id="olive-fold" x1="0" y1="0" x2="1" y2="0">
          <stop offset="0" stop-color="var(--olive-dark)"/>
          <stop offset="0.5" stop-color="var(--olive-light)"/>
          <stop offset="1" stop-color="var(--olive-dark)"/>
        </linearGradient>
        <linearGradient id="white-fold" x1="0" y1="0" x2="1" y2="1">
          <stop offset="0" stop-color="#ffffff"/>
          <stop offset="1" stop-color="#e4e4e4"/>
        </linearGradient>
      </defs>
      <path d="M0 0 H1160 V22 L830 31 L700 20 L580 18 L290 32 L0 18Z" fill="var(--band)"/>
      <polyline points="0,20 290,34 580,20 700,22 830,33 1160,24" fill="none" stroke="var(--string)" stroke-width="2"/>

      <g class="flag"><path d="M29 22 L91 25 L60 97Z" fill="url(#white-fold)"/><text class="flag-name" x="60" y="40">FERNLEA</text><circle cx="60" cy="55" r="9" fill="none" stroke="var(--ink)" stroke-width="1"/></g>
      <g class="flag"><path d="M151 27 L213 31 L182 97Z" fill="url(#olive-fold)"/></g>
      <g class="flag"><path d="M293 33 L355 31 L324 120Z" fill="url(#white-fold)"/><text class="flag-name" x="324" y="50">FERNLEA</text><circle cx="324" cy="65" r="9" fill="none" stroke="var(--ink)" stroke-width="1"/></g>
      <g class="flag"><path d="M442 27 L504 24 L473 95Z" fill="url(#olive-fold)"/></g>
      <g class="flag"><path d="M656 22 L718 23 L687 92Z" fill="url(#olive-fold)"/></g>
      <g class="flag"><path d="M805 30 L867 34 L836 118Z" fill="url(#white-fold)"/><text class="flag-name" x="836" y="51">FERNLEA</text><circle cx="836" cy="66" r="9" fill="none" stroke="var(--ink)" stroke-width="1"/></g>
      <g class="flag"><path d="M947 31 L1009 28 L978 99Z" fill="url(#olive-fold)"/></g>
      <g class="flag"><path d="M1070 26 L1132 24 L1101 97Z" fill="url(#white-fold)"/><text class="flag-name" x="1101" y="43">FERNLEA</text><circle cx="1101" cy="58" r="9" fill="none" stroke="var(--ink)" stroke-width="1"/></g>

      <g class="crest">
        <circle cx="579" cy="72" r="44" fill="var(--flag-white)" stroke="var(--string)" stroke-width="3"/>
        <text class="crest-name" x="579" y="77">FERNLEA</text>
      </g>
    </svg>
  </section>

  <!-- Joined section, left half -->
  <section class="pen-panel pen-panel--left">
    <div class="meadow" role="img" aria-label="Meadow of wild flowers at varied heights: thistles, poppies, cornflowers, tansy, willowherb and daisies in grass"></div>
    <svg class="bunting" viewBox="0 0 576 167">
      <path d="M0 0 H576 V18 L180 26 L0 20Z" fill="var(--band)"/>
      <polyline points="0,22 180,28 576,20" fill="none" stroke="var(--string)" stroke-width="2"/>
      <g class="crest">
        <circle cx="19" cy="72" r="44" fill="var(--flag-white)" stroke="var(--string)" stroke-width="3"/>
        <text class="crest-name" x="19" y="77">FERNLEA</text>
      </g>
      <g class="flag"><path d="M75 26 L137 27 L106 96Z" fill="url(#olive-fold)"/></g>
      <g class="flag"><path d="M223 26 L285 25 L254 120Z" fill="url(#white-fold)"/><text class="flag-name" x="254" y="44">FERNLEA</text><circle cx="254" cy="59" r="9" fill="none" stroke="var(--ink)" stroke-width="1"/></g>
      <g class="flag"><path d="M366 25 L428 24 L397 96Z" fill="url(#olive-fold)"/></g>
      <g class="flag"><path d="M488 22 L550 21 L519 96Z" fill="url(#white-fold)"/><text class="flag-name" x="519" y="39">FERNLEA</text><circle cx="519" cy="54" r="9" fill="none" stroke="var(--ink)" stroke-width="1"/></g>
    </svg>
  </section>

  <!-- Joined section, right half -->
  <section class="pen-panel pen-panel--right">
    <div class="meadow" role="img" aria-label="Meadow of wild flowers at varied heights: thistles, poppies, cornflowers, tansy, willowherb and daisies in grass"></div>
    <svg class="bunting" viewBox="0 0 581 167">
      <path d="M0 0 H581 V24 L330 30 L150 28 L0 18Z" fill="var(--band)"/>
      <polyline points="0,20 150,30 330,32 581,26" fill="none" stroke="var(--string)" stroke-width="2"/>
      <g class="flag"><path d="M28 23 L90 27 L59 96Z" fill="url(#white-fold)"/><text class="flag-name" x="59" y="42">FERNLEA</text><circle cx="59" cy="57" r="9" fill="none" stroke="var(--ink)" stroke-width="1"/></g>
      <g class="flag"><path d="M151 30 L213 31 L182 100Z" fill="url(#olive-fold)"/></g>
      <g class="flag"><path d="M293 32 L355 31 L324 122Z" fill="url(#white-fold)"/><text class="flag-name" x="324" y="50">FERNLEA</text><circle cx="324" cy="65" r="9" fill="none" stroke="var(--ink)" stroke-width="1"/></g>
      <g class="flag"><path d="M441 29 L503 28 L472 98Z" fill="url(#olive-fold)"/></g>
      <g class="crest">
        <circle cx="576" cy="72" r="44" fill="var(--flag-white)" stroke="var(--string)" stroke-width="3"/>
        <text class="crest-name" x="576" y="77">FERNLEA</text>
      </g>
    </svg>
  </section>

</main>
</body>
</html>
```